Bubble-Diagramm als Infografik für unseren Kunden aus der Immobilienbranche
Zielgruppe
Wir sind ein Software-Unternehmen mit Kunden aus allen Branchen. Ganz generell für unsere Homepage, konkret aber auch im Rahmen eines Kundenprojektes suchen wir ansprechende Beispiele und kreative Visualisierungen, wie Diagramme zu bestimmten Sachverhalten dargestellt werden können.
Aufgabenstellung
Wir möchten die Möglichkeiten darstellen, mit excelbasierten Diagrammtypen den gewissen „Wow-Effekt“ bei unseren Kunden hervorzurufen. Konkret geht es uns hier um die Erstellung eines Bubble-Diagramms. In einem Objektvergleich von Gewerbeimmobilien sollen drei Dimensionen (hier: Größe des Objekte, Gesamtmiete über die Laufzeit, effektive Miete je Quadratmeter) im Bubble-Diagramm dargestellt werden. Siehe hierzu Entwurf (.xls-Datei) anbei.
Eine Orientierung an unserem Firmenlayout (www.molten-it.de) ist ausdrücklich erwünscht. Die Grafik sollte aufgeräumt und klar wirken, ohne nüchtern zu sein, um auf der einen Seite mit der Form nicht vom Inhalt abzulenken, und sich auf der anderen Seite aber eben doch über die Form von der Konkurrenz, die nur mit Excel-Bordmitteln arbeitet, erkennbar abzuheben. Denkbar sind grundsätzlich auch Piktogramme oder vergleichbare, Inhalt transportierende Elemente im Graphik-Hintergrund oder in der Umrahmung, immer unter der Maßgabe, dass sie nicht zu verspielt daherkommen.
Technisch sind wir in der Lage, Excel-Diagramme auch „interaktiv“ zu gestalten, also nach Klick auf ein Diagrammelement ein Kontextmenü oder erweiterte Informationen einzublenden. Daher wünschen wir uns als Teil des Entwurfs, beispielhaft für eine Blase, die Darstellung so eines interaktiven Elements: eines Kontextmenüs / und oder eines Datenblatts.
Vorzugsweise soll die Grafik im Excel-Format zur Verfügung gestellt werden, das ist aber kein Must-have.

```html
<!DOCTYPE html>
<html lang="de">
<head>
<meta charset="utf-8">
<title>Bubble-Diagramm Objektvergleich</title>
<link href="https://fonts.googleapis.com/css2?family=Michroma&family=Questrial&display=swap" rel="stylesheet">
<style>
  :root {
    --page: #ffffff;
    --panel: #f3f3f3;
    --panel-center: #fbfbfb;
    --band: #e6e6e6;
    --axis: #666666;
    --guide: #cfcfcf;
    --bubble: #ababab;
    --ring: #b3b3b3;
    --text: #8a8a8a;
    --label: #7a7a7a;
    --scene: #ececec;
    --icon: #d9d9d9;
  }
  html, body {
    margin: 0;
    padding: 0;
    width: 900px;
    height: 1200px;
    overflow: hidden;
    background: var(--page);
  }
  .canvas {
    position: relative;
    width: 900px;
    height: 1200px;
    display: flex;
    align-items: center;
    justify-content: center;
  }
  .chart {
    width: 900px;
    height: 506px;
    display: block;
  }
  .value-label { font-family: "Michroma", sans-serif; fill: var(--label); }
  .value-label .euro {
    font-family: "Questrial", sans-serif;
    font-size: 22px;
    font-weight: 700;
  }
  .unit-small { font-size: 11px; }
  .axis-title, .legend-text, .tooltip-text {
    font-family: "Questrial", sans-serif;
    fill: var(--text);
  }
</style>
</head>
<body>
<main class="canvas">
  <svg class="chart" viewBox="0 0 1456 818" xmlns="http://www.w3.org/2000/svg" aria-label="Bubble-Diagramm: Effektivmiete je m² über Gesamtmiete, Blasengröße zeigt Objektgröße">
    <defs>
      <radialGradient id="panelGlow" cx="50%" cy="50%" r="60%">
        <stop offset="0%" stop-color="var(--panel-center)"/>
        <stop offset="100%" stop-color="var(--panel)"/>
      </radialGradient>
    </defs>

    <rect class="panel" width="1456" height="818" fill="url(#panelGlow)"/>

    <g class="frame-bands" fill="var(--band)">
      <polygon points="46,0 84,0 84,337 46,375"/>
      <polygon points="46,357 84,357 84,818 46,818"/>
      <polygon points="0,748 498,748 530,785 0,785"/>
      <polygon points="732,748 1456,748 1456,785 764,785"/>
    </g>

    <rect class="skyline-scene" x="253" y="115" width="1065" height="505" rx="4" fill="var(--scene)" opacity="0.55" role="img" aria-label="Feine Linienzeichnung einer Stadtsilhouette mit Wolken"/>

    <g class="guides" stroke="var(--guide)" stroke-width="2" fill="none">
      <line x1="752" y1="123" x2="752" y2="652"/>
      <line x1="248" y1="355" x2="1318" y2="355"/>
      <line x1="253" y1="645" x2="1310" y2="180" stroke-width="1.5"/>
    </g>

    <g class="axes" stroke="var(--axis)" stroke-width="5" stroke-linecap="round">
      <line x1="248" y1="72" x2="248" y2="715"/>
      <line x1="168" y1="652" x2="1283" y2="652"/>
    </g>

    <g class="y-labels value-label" font-size="19">
      <text x="153" y="64">20<tspan class="euro">€</tspan></text>
      <text x="153" y="348">20<tspan class="euro">€</tspan></text>
      <text x="153" y="642">15<tspan class="euro">€</tspan></text>
    </g>

    <g class="x-labels value-label" font-size="19">
      <text x="258" y="717">5<tspan class="unit-small">MIO</tspan> <tspan class="euro">€</tspan></text>
      <text x="760" y="717">10<tspan class="unit-small">MIO</tspan> <tspan class="euro">€</tspan></text>
      <text x="1291" y="717">15<tspan class="unit-small">MIO</tspan> <tspan class="euro">€</tspan></text>
    </g>

    <text class="axis-title" x="624" y="776" font-size="25" text-anchor="middle">Gesamtmiete</text>
    <text class="axis-title" x="0" y="0" font-size="24" text-anchor="middle" transform="translate(74 225) rotate(-90)">Effektivmiete je m²</text>

    <g class="legend">
      <circle cx="986" cy="57" r="25" fill="none" stroke="var(--ring)" stroke-width="2"/>
      <path d="M986,57 L1004,57 A18 18 0 1 1 986,39 Z" fill="var(--bubble)"/>
      <rect x="990" y="36" width="15" height="17" fill="var(--icon)" role="img" aria-label="Gebäude-Symbol"/>
      <text class="legend-text" x="1428" y="63" font-size="17" text-anchor="end" letter-spacing="0.5">Die Größe der Blasen zeigt die Objektgröße an.</text>
    </g>

    <g class="bubble bubble-1">
      <circle cx="550" cy="469" r="82" fill="none" stroke="var(--ring)" stroke-width="2"/>
      <path d="M550,469 L613,469 A63 63 0 1 1 550,406 Z" fill="var(--bubble)"/>
      <rect x="554" y="384" width="60" height="66" fill="var(--icon)" role="img" aria-label="Bürogebäude-Symbol"/>
      <circle cx="547" cy="388" r="6" fill="var(--bubble)"/>
      <circle cx="628" cy="452" r="6" fill="var(--bubble)"/>
    </g>
    <g class="bubble bubble-2">
      <circle cx="691" cy="413" r="64" fill="none" stroke="var(--ring)" stroke-width="2"/>
      <path d="M691,413 L742,413 A51 51 0 1 1 691,362 Z" fill="var(--bubble)"/>
      <rect x="694" y="345" width="46" height="52" fill="var(--icon)" role="img" aria-label="Bürogebäude-Symbol"/>
      <circle cx="690" cy="349" r="6" fill="var(--bubble)"/>
    </g>
    <g class="bubble bubble-3">
      <circle cx="801" cy="368" r="82" fill="none" stroke="var(--ring)" stroke-width="2"/>
      <path d="M801,368 L864,368 A63 63 0 1 1 801,305 Z" fill="var(--bubble)"/>
      <rect x="805" y="276" width="64" height="74" fill="var(--icon)" role="img" aria-label="Bürogebäude-Symbol"/>
      <circle cx="798" cy="288" r="6" fill="var(--bubble)"/>
      <circle cx="879" cy="351" r="6" fill="var(--bubble)"/>
    </g>
    <g class="bubble bubble-4">
      <circle cx="1014" cy="345" r="99" fill="none" stroke="var(--ring)" stroke-width="2"/>
      <path d="M1014,345 L1091,345 A77 77 0 1 1 1014,268 Z" fill="var(--bubble)"/>
      <rect x="1018" y="236" width="76" height="86" fill="var(--icon)" role="img" aria-label="Bürogebäude-Symbol"/>
      <circle cx="1010" cy="246" r="6" fill="var(--bubble)"/>
      <circle cx="1108" cy="322" r="6" fill="var(--bubble)"/>
    </g>

    <g class="tooltip">
      <line x1="433" y1="232" x2="433" y2="300" stroke="var(--guide)" stroke-width="1.5"/>
      <line x1="520" y1="237" x2="606" y2="237" stroke="var(--guide)" stroke-width="1.5"/>
      <polyline points="292,310 508,310 538,380" fill="none" stroke="var(--guide)" stroke-width="1.5"/>
      <g class="tooltip-text" font-size="20">
        <text x="292" y="247">Effektivmiete</text>
        <text x="292" y="272">Gesamtmiete</text>
        <text x="292" y="296">Größe</text>
        <text x="443" y="247">20.30€</text>
        <text x="443" y="272">8mio€</text>
        <text x="443" y="296">8000m<tspan font-size="10" dy="-8">2</tspan></text>
      </g>
    </g>
  </svg>
</main>
</body>
</html>
```